Road Construction Company needs business cards

We would like a new business card designed for our business.

We're a road construction company based in Qld, Australia.

Can the business card please have the following information on it.

Name: Warren Halbeck
Position: General Manager
Phone: 0472 915 348
Email: Warren.halbeck@tovrin.com.au
Address: 87 Marrow Ave, Pendlebay, QLD, 4023
Website: www.tovrin.com.au

Visually we'd like the card to be professional and simple.

Attached is our logo.

Our website is www.tovrin.com.au

Target Market(s)

Men aged 25-60

Contact Information for Business Card

As listed in project description

Font styles to use
Serif

Requirements
Must have
• Large logo on back of card

```html
<!DOCTYPE html>
<html lang="en">
<head>
<meta charset="utf-8">
<title>Tovrin Road Construction – Business Card</title>
<link rel="stylesheet" href="https://fonts.googleapis.com/css2?family=Noto+Serif:wght@400;700&display=swap">
<style>
  :root {
    --backdrop: #474747;
    --card-dark: #181818;
    --card-blue: #0557a5;
    --brand-blue: #0b5aa8;
    --accent-sky: #35a6dc;
    --text-light: #f2f2f2;
    --serif: "Noto Serif", Georgia, serif;
  }
  * { box-sizing: border-box; margin: 0; padding: 0; }
  html, body {
    width: 1200px; height: 801px; overflow: hidden;
    background: var(--backdrop);
    font-family: var(--serif);
  }
  .sheet {
    width: 1200px; height: 801px;
    display: flex; align-items: center; justify-content: center; gap: 44px;
  }
  .card {
    position: relative;
    width: 540px; height: 309px;
    border-radius: 18px;
    overflow: hidden;
    border-bottom: 3px solid var(--accent-sky);
    box-shadow: 0 14px 30px rgba(0,0,0,.35);
  }

  /* Front */
  .card--front { background: var(--card-dark); color: var(--text-light); }
  .front-wordmark {
    position: absolute; top: 48px; left: 0; right: 0;
    text-align: center;
    font-weight: 700; font-size: 40px; letter-spacing: 1px;
    color: var(--brand-blue);
    line-height: 1.1;
  }
  .front-wordmark small { display: block; font-size: 17px; letter-spacing: 5px; }
  .edge-marker {
    position: absolute; left: 0; top: 176px;
    width: 22px; height: 38px;
    background: var(--accent-sky);
  }
  .person { position: absolute; left: 44px; top: 166px; }
  .person-name { font-weight: 700; font-size: 21px; color: var(--accent-sky); line-height: 1.15; }
  .person-role { font-size: 13px; line-height: 1.3; }
  .divider {
    position: absolute; left: 44px; right: 22px; top: 220px;
    height: 1px; background: var(--accent-sky);
  }
  .contacts {
    position: absolute; left: 44px; top: 230px;
    list-style: none; font-size: 12.5px; line-height: 21px;
  }
  .contacts li { display: flex; align-items: center; gap: 8px; }
  .contacts svg { width: 11px; height: 11px; fill: var(--accent-sky); flex: none; }
  .address {
    position: absolute; right: 30px; top: 232px;
    font-size: 12.5px; line-height: 19px; text-align: left;
  }

  /* Back */
  .card--back { background: var(--card-blue); }
  .back-wordmark {
    position: absolute; inset: 0;
    display: flex; flex-direction: column; align-items: center; justify-content: center;
    font-weight: 700; font-size: 54px; letter-spacing: 1px;
    color: #ffffff; line-height: 1.1;
  }
  .back-wordmark small { font-size: 21px; letter-spacing: 7px; }
</style>
</head>
<body>
<main class="sheet">
  <section class="card card--front" aria-label="Business card front">
    <div class="front-wordmark">Tovrin<small>ROAD CONSTRUCTION</small></div>
    <div class="edge-marker"></div>
    <div class="person">
      <p class="person-name">Warren Halbeck</p>
      <p class="person-role">General Manager</p>
    </div>
    <div class="divider"></div>
    <ul class="contacts">
      <li>
        <svg viewBox="0 0 12 12" aria-hidden="true"><path d="M2.5 1l2 2.2-1 1.3a7 7 0 0 0 4 4l1.3-1 2.2 2-1.2 1.5C5.5 11 1 6.5 1 2.2z"/></svg>
        0472 915 348
      </li>
      <li>
        <svg viewBox="0 0 12 12" aria-hidden="true"><path d="M1 2.5h10v7H1z M1.6 3l4.4 3.4L10.4 3" stroke="#181818" stroke-width=".9"/></svg>
        Warren.halbeck@tovrin.com.au
      </li>
      <li>
        <svg viewBox="0 0 12 12" aria-hidden="true"><circle cx="6" cy="6" r="5"/><path d="M1 6h10M6 1c-2.5 2.8-2.5 7.2 0 10M6 1c2.5 2.8 2.5 7.2 0 10" stroke="#181818" stroke-width=".8" fill="none"/></svg>
        www.tovrin.com.au
      </li>
    </ul>
    <p class="address">87 Marrow Ave,<br>Pendlebay, QLD, 4023</p>
  </section>

  <section class="card card--back" aria-label="Business card back">
    <div class="back-wordmark">Tovrin<small>ROAD CONSTRUCTION</small></div>
  </section>
</main>
</body>
</html>
```